Business Card Design for a Personal Trainer

I need a business card design for my job as a personal trainer. It should have a unique, modern and exclusive design. On the front there should be only my logo with my name and my job. 0162/3819204 Tobias Lendhart Wiesengrundweg 14 80417 Munich Germany The most important contact information is the web adress. it can be bigger than the rest, but its not necessary. The card should be 8,5cmx5,5cm big. Font: Roboto. Colors: black, white, gray, 56c1ff.

```html
<!DOCTYPE html>
<html lang="de">
<head>
<meta charset="utf-8">
<title>Tobias Lendhart – Personal Trainer Visitenkarte</title>
<link href="https://fonts.googleapis.com/css2?family=Roboto:wght@400;500&display=swap" rel="stylesheet">
<style>
  :root {
    --stage: #e8e5e1;
    --sky: #56c1ff;
    --ink: #231f20;
    --white: #ffffff;
    --photo-light: #d9d9d9;
    --photo-dark: #4a4a4a;
  }
  * { box-sizing: border-box; margin: 0; padding: 0; }
  html, body { width: 1200px; height: 900px; overflow: hidden; }
  body {
    position: relative;
    background: var(--stage);
    font-family: "Roboto", Arial, sans-serif;
    color: var(--white);
  }
  .card { position: absolute; }
  .card--front { left: 330px; top: 90px; width: 555px; height: 343px; background: var(--sky); }
  .card--back { left: 330px; top: 469px; width: 559px; height: 344px; background: var(--ink); }

  .portrait {
    position: absolute; left: 27px; top: 53px; width: 216px; height: 225px;
    background: linear-gradient(180deg, var(--photo-light) 0%, #bdbdbd 55%, var(--photo-dark) 100%);
  }

  .identity { position: absolute; left: 268px; top: 66px; width: 266px; text-align: center; }
  .identity__name { font-size: 29px; font-weight: 400; letter-spacing: 0.5px; line-height: 1; white-space: nowrap; }
  .identity__role {
    display: flex; align-items: center; gap: 6px; margin-top: 6px;
    font-size: 11.5px; letter-spacing: 2.6px; line-height: 1; white-space: nowrap;
  }
  .identity__role::before, .identity__role::after {
    content: ""; flex: 1; height: 1px; background: currentColor;
  }

  .contact { position: absolute; left: 270px; top: 150px; list-style: none; }
  .contact__item { display: flex; align-items: center; gap: 6px; font-size: 17px; line-height: 23px; }
  .contact__icon { width: 17px; height: 17px; flex: none; }

  .address { position: absolute; left: 273px; top: 230px; font-style: normal; font-size: 17px; line-height: 23px; }

  .brand { position: absolute; left: 0; right: 0; top: 196px; display: flex; justify-content: center; }
  .brand__inner { display: flex; flex-direction: column; align-items: stretch; }
  .brand__name { display: flex; align-items: center; gap: 12px; font-size: 32px; font-weight: 400; letter-spacing: 0.5px; line-height: 1; white-space: nowrap; }
  .brand__square { width: 14px; height: 14px; background: var(--white); flex: none; }
  .brand__role {
    display: flex; align-items: center; gap: 6px; margin-top: 8px;
    font-size: 13px; letter-spacing: 3px; line-height: 1; white-space: nowrap;
  }
  .brand__role::before, .brand__role::after { content: ""; flex: 1; height: 1px; background: currentColor; }
</style>
</head>
<body>
  <section class="card card--front" aria-label="Vorderseite">
    <div class="portrait" role="img" aria-label="Schwarz-weißes Porträtfoto des Personal Trainers"></div>

    <div class="identity">
      <h1 class="identity__name">TOBIAS LENDHART</h1>
      <p class="identity__role">PERSONAL TRAINER</p>
    </div>

    <ul class="contact">
      <li class="contact__item">
        <svg class="contact__icon" viewBox="0 0 24 24" aria-hidden="true"><path fill="#fff" d="M3 9c0-3 4-5 9-5s9 2 9 5v2h-5V9c-1-1-7-1-8 0v2H3zM6 12h12l2 8H4zM12 14a2.5 2.5 0 100 5 2.5 2.5 0 000-5z"/></svg>
        <span>0162/3819204</span>
      </li>
      <li class="contact__item">
        <svg class="contact__icon" viewBox="0 0 24 24" aria-hidden="true"><path fill="#fff" d="M2 5h20v14H2z"/><path fill="none" stroke="#56c1ff" stroke-width="1.8" d="M2.5 5.5 12 13l9.5-7.5M2.5 18.5l7-6.5M21.5 18.5l-7-6.5"/></svg>
        <span>t.lendhart@postfach.de</span>
      </li>
      <li class="contact__item">
        <svg class="contact__icon" viewBox="0 0 24 24" aria-hidden="true"><circle cx="12" cy="12" r="9.5" fill="#fff"/><path fill="#56c1ff" d="M7 7c2 0 3 1 3 3s-2 2-2 4-2 1-3 0c0-3 0-5 2-7zM14 12c2-1 4 0 4 2s-2 4-4 4 0-4 0-6z"/></svg>
        <span>www.tobiaslendhart.de</span>
      </li>
    </ul>

    <address class="address">Wiesengrundweg 14<br>80417 München</address>
  </section>

  <section class="card card--back" aria-label="Rückseite">
    <div class="brand">
      <div class="brand__inner">
        <p class="brand__name"><span class="brand__square" aria-hidden="true"></span>TOBIAS LENDHART</p>
        <p class="brand__role">PERSONAL TRAINER</p>
      </div>
    </div>
  </section>
</body>
</html>
```